Falkrin homes and renovations business card design.

Would like some new card designs utilizing my new logo that look professional. I am open to different colors on the logo or utilize the same ones we have. I like the original concept but would like to see some fresh ideas and build on what we have already done.

Target Market(s)

Custom home building industry, Real estate sales, Renovation projects.

Industry/Entity Type

Home Builder

Contact Information for Business Card

Falkrin Homes and Renovations
2871 96th Avenue
Halvik, Northmere
T2R3W8
Home : 403- 718-4063 Cell: 403- 294-5170

My info is : Dax Falkrin, President and CEO
email: falkrinhomes@maildrop-example.net
Website: falkrinhomes-example.com
websit

Requirements
Must have
• Must Use my new logo design. I am open to different colors on the logo or utilize the same ones in the existing design. I can upload the original logo design if needed.

```html
<!DOCTYPE html>
<html lang="en">
<head>
<meta charset="utf-8">
<title>Falkrin Homes and Renovations – Business Card</title>
<link href="https://fonts.googleapis.com/css2?family=Open+Sans:wght@400;600;700&display=swap" rel="stylesheet">
<style>
  :root {
    --stage: #000000;
    --card: #333335;
    --card-light: #3b3b3e;
    --gold: #c8963a;
    --yellow: #f2c21b;
    --text: #f1f1f1;
    --divider: #4a4a4d;
  }
  * { margin: 0; padding: 0; box-sizing: border-box; }
  html, body {
    width: 1200px; height: 900px; overflow: hidden;
    background: var(--stage);
    font-family: "Open Sans", Arial, sans-serif;
  }
  .stage { position: relative; width: 1200px; height: 900px; }
  .card {
    position: absolute; top: 271px; width: 457px; height: 281px;
    border-radius: 14px;
    background: radial-gradient(ellipse at 50% 40%, var(--card-light), var(--card) 75%);
  }
  .card--front { left: 137px; }
  .card--back { left: 626px; }

  .brand-mark {
    position: absolute; display: flex; align-items: center; gap: 8px;
    color: var(--gold); font-weight: 700; letter-spacing: 2px; text-transform: uppercase;
  }
  .card--front .brand-mark { left: 40px; top: 120px; width: 145px; justify-content: center; font-size: 20px; }
  .card--back .brand-mark { left: 0; right: 0; top: 125px; justify-content: center; font-size: 40px; gap: 14px; }
  .brand-square { width: 10px; height: 10px; background: var(--gold); }
  .card--back .brand-square { width: 16px; height: 16px; }

  .divider {
    position: absolute; left: 210px; top: 78px; width: 1px; height: 160px;
    background: linear-gradient(to bottom, transparent, var(--divider), transparent);
  }
  .details { position: absolute; left: 222px; top: 40px; color: var(--text); }
  .person-name { color: var(--gold); font-size: 16px; font-weight: 600; line-height: 20px; margin-left: 1px; }
  .person-title { font-size: 12.5px; line-height: 17px; }
  .company-name { color: var(--yellow); font-size: 14px; font-weight: 600; margin-top: 14px; line-height: 20px; }
  .address { font-size: 12.5px; line-height: 19px; }
  .contact-list { list-style: none; margin-top: 11px; }
  .contact-list li { display: flex; align-items: center; gap: 8px; font-size: 12.5px; line-height: 19px; }
  .contact-list svg { width: 9px; height: 9px; fill: var(--gold); flex: none; }
  .contact-list .email { font-size: 11.8px; }
</style>
</head>
<body>
<div class="stage">
  <section class="card card--front">
    <div class="brand-mark"><span class="brand-square"></span>Falkrin</div>
    <div class="divider"></div>
    <div class="details">
      <p class="person-name">Dax Falkrin</p>
      <p class="person-title">President and CEO</p>
      <p class="company-name">Falkrin homes and Renovations</p>
      <p class="address">2871 96th Avenue Halvik, Northmere<br>T2R3W8</p>
      <ul class="contact-list">
        <li><svg viewBox="0 0 10 10"><path d="M2 0.5 L3.6 2.6 L2.7 3.6 Q3.8 6 6.4 7.3 L7.4 6.4 L9.5 8 L8.3 9.5 Q1.5 8 0.5 1.7 Z"/></svg>403- 718-4063</li>
        <li><svg viewBox="0 0 10 10"><path d="M2.5 0 H7.5 V10 H2.5 Z M3.3 1 V8 H6.7 V1 Z"/></svg>403- 294-5170</li>
        <li class="email"><svg viewBox="0 0 10 10"><path d="M0 2 H10 V8.5 H0 Z M0.8 2.6 L5 5.6 L9.2 2.6 Z"/></svg>falkrinhomes@maildrop-example.net</li>
        <li><svg viewBox="0 0 10 10"><circle cx="5" cy="5" r="4.5"/></svg>falkrinhomes-example.com</li>
      </ul>
    </div>
  </section>

  <section class="card card--back">
    <div class="brand-mark"><span class="brand-square"></span>Falkrin</div>
  </section>
</div>
</body>
</html>
```